MRT Property - Business Cards

Looking for a business card & general letterhead, signage etc design for our new logo.

Colours:
000a20
0056a2
00b5ef
0088ce
68cef2

Fonts:
Poppins
Karla

Please keep look and feel of new brand - example in the zip package I sent.

```html
<!DOCTYPE html>
<html lang="en">
<head>
<meta charset="utf-8">
<title>MRT Property – Business Cards</title>
<link href="https://fonts.googleapis.com/css2?family=Montserrat:wght@400;500;700&display=swap" rel="stylesheet">
<style>
  :root {
    --ink: #000a20;
    --navy-card: #0d1326;
    --blue-deep: #0056a2;
    --blue-cyan: #00b5ef;
    --blue-mid: #0088ce;
    --blue-light: #68cef2;
    --paper: #ffffff;
    --text-dark: #1a1a1a;
    --backdrop: #4a4a4a;
  }
  * { margin: 0; padding: 0; box-sizing: border-box; }
  html, body {
    width: 1200px; height: 689px; overflow: hidden;
    background: var(--backdrop);
    font-family: "Montserrat", sans-serif;
  }
  .stage {
    position: relative; width: 1200px; height: 689px;
    display: flex; align-items: center; justify-content: center; gap: 50px;
  }
  .card {
    position: relative; width: 520px; height: 297px;
    box-shadow: 0 10px 30px rgba(0,0,0,.35);
  }
  .card--front {
    background: var(--navy-card);
    display: flex; align-items: center; justify-content: center;
  }
  .brand {
    display: flex; align-items: center; gap: 14px;
    color: var(--blue-deep); font-weight: 700; white-space: nowrap;
  }
  .brand__dot { border-radius: 50%; background: var(--blue-deep); flex: none; }
  .card--front .brand { font-size: 50px; }
  .card--front .brand__dot { width: 34px; height: 34px; }

  .card--back { background: var(--paper); color: var(--text-dark); }
  .card--back .brand {
    position: absolute; left: 28px; top: 64px; font-size: 25px; gap: 10px;
  }
  .card--back .brand__dot { width: 18px; height: 18px; }

  .person { position: absolute; right: 36px; top: 42px; text-align: right; }
  .person__name {
    color: var(--blue-deep); font-weight: 700; font-size: 19px; letter-spacing: .3px;
  }
  .person__role { font-size: 12px; font-weight: 500; letter-spacing: .4px; margin-top: 2px; }
  .accent-bar {
    position: absolute; right: 0; top: 42px; width: 10px; height: 34px;
    background: var(--blue-deep);
  }
  .divider {
    position: absolute; right: 36px; top: 98px; width: 200px; height: 1px;
    background: var(--text-dark);
  }
  .address {
    position: absolute; right: 36px; top: 112px; text-align: right;
    font-size: 12.5px; line-height: 1.5;
  }
  .contact {
    position: absolute; left: 30px; bottom: 26px;
    border-top: 1px solid var(--text-dark); padding-top: 8px; width: 260px;
    list-style: none; font-size: 12.5px; line-height: 1.7;
  }
  .contact li { display: flex; align-items: center; gap: 10px; }
  .contact svg { width: 13px; height: 13px; flex: none; fill: var(--blue-deep); }
</style>
</head>
<body>
<main class="stage">
  <section class="card card--front" aria-label="Business card front">
    <div class="brand"><span class="brand__dot"></span>MRT Property</div>
  </section>

  <section class="card card--back" aria-label="Business card back">
    <div class="brand"><span class="brand__dot"></span>MRT Property</div>

    <div class="person">
      <p class="person__name">DANIEL REEVE</p>
      <p class="person__role">MANAGING DIRECTOR</p>
    </div>
    <span class="accent-bar"></span>
    <span class="divider"></span>
    <p class="address">18 Harbour View Road<br>40210, Westmere</p>

    <ul class="contact">
      <li>
        <svg viewBox="0 0 16 16" aria-hidden="true"><path d="M3.5 1l3 3-1.8 1.8a9 9 0 0 0 5.5 5.5L12 9.5l3 3-2 2.5C6.5 15 1 9.5 1 3z"/></svg>
        044-555 010 220
      </li>
      <li>
        <svg viewBox="0 0 16 16" aria-hidden="true"><path d="M1 3h14v10H1z M1 3l7 6 7-6" fill="none" stroke="#0056a2" stroke-width="1.6"/></svg>
        hello@mrtproperty.com
      </li>
      <li>
        <svg viewBox="0 0 16 16" aria-hidden="true"><g fill="none" stroke="#0056a2" stroke-width="1.4"><circle cx="8" cy="8" r="6.5"/><ellipse cx="8" cy="8" rx="2.8" ry="6.5"/><path d="M1.5 8h13"/></g></svg>
        www.mrtproperty.com
      </li>
    </ul>
  </section>
</main>
</body>
</html>
```